Web page design for a startup, no coding

Quorvix is a Data mining startup helping companies get data from websites. We’re looking to revamp our website to make it more professional and conversation friendly.
I need a designer to design the website in PSD and Once the PSD is done, the HTML design will be awarded as a separate job. We’ll need continues improvements to the design based on the user behaviour in the site and this can be a long term work for the right designer.
Read the details on the attached document
Target Market(s)
Big data, Data Mining
Industry/Entity Type
Business Software
Number of Pages Required
5+ page
Requirements
Must have
- Refer to the doc
Nice to have
- Refer to the doc
Should not have
- Refer to the doc

```html
<!DOCTYPE html>
<html lang="en">
<head>
<meta charset="utf-8">
<title>Quorvix — Turn Websites Into Structured Data Feeds</title>
<link rel="stylesheet" href="https://fonts.googleapis.com/css2?family=Oswald:wght@400;500&family=Open+Sans:wght@400;600;700&family=Roboto:wght@300;400;500&display=swap">
<style>
:root{
  --navy:#0c1a2e;
  --blue:#2f6fb8;
  --blue-band:#3d7cc4;
  --ink:#333333;
  --muted:#777777;
  --pale:#eef4fa;
  --footer:#141414;
  --footer-bar:#0a0a0a;
  --white:#ffffff;
}
*{margin:0;padding:0;box-sizing:border-box}
html,body{width:1200px;height:3072px;overflow:hidden}
body{position:relative;background:var(--white);font-family:"Open Sans",Arial,sans-serif;color:var(--ink)}
.abs{position:absolute}

/* hero */
.hero{position:absolute;left:0;top:0;width:1200px;height:606px;overflow:hidden}
.hero-photo{position:absolute;left:0;top:0;width:1200px;height:606px;
  background:radial-gradient(ellipse at 75% 55%,#2a4366 0%,#152a47 40%,var(--navy) 80%)}
.brand{position:absolute;left:98px;top:58px;color:var(--white);font-family:"Open Sans",Arial,sans-serif;font-size:40px;font-weight:400;letter-spacing:.5px}
.nav{position:absolute;top:45px;left:702px;color:var(--white);font-family:"Roboto",Arial,sans-serif;font-size:12.5px;font-weight:500}
.nav span{position:absolute;white-space:nowrap}
.hero h1{position:absolute;left:98px;top:200px;width:420px;color:var(--white);font-family:"Oswald",Arial,sans-serif;font-weight:400;font-size:40px;line-height:46px}
.hero p{position:absolute;left:98px;top:307px;width:380px;color:#dfe6ef;font-size:12.5px;line-height:20px}
.btn{position:absolute;background:var(--blue);color:var(--white);font-size:14px;display:flex;align-items:center;justify-content:center;border-radius:2px}
.hero-dots{position:absolute;left:570px;top:541px;display:flex;gap:7px}
.hero-dots i{width:13px;height:13px;border:1.5px solid var(--white);border-radius:50%}
.hero-dots i:first-child{background:var(--white)}

/* section heads */
.sec-title{position:absolute;left:0;width:1200px;text-align:center;font-family:"Roboto",Arial,sans-serif;font-weight:300;font-size:30px;color:#2b2b2b;letter-spacing:.5px}
.sec-rule{position:absolute;left:576px;width:48px;height:3px;background:var(--blue)}

/* why us */
.why{position:absolute;left:0;top:606px;width:1200px;height:475px;background:var(--white)}
.feature{position:absolute;width:240px;text-align:center}
.feature .ring{width:98px;height:98px;margin:0 auto;border:1.5px solid #5b8fc9;border-radius:50%;background:var(--white);display:flex;align-items:center;justify-content:center}
.feature h3{margin-top:22px;font-family:"Roboto",Arial,sans-serif;font-weight:400;font-size:18px;color:#333}
.feature p{margin-top:10px;font-size:11px;line-height:18px;color:var(--muted)}
.feature .more{margin-top:14px;font-family:"Roboto",Arial,sans-serif;font-size:12px;font-weight:500;color:#222}

/* offerings */
.offer{position:absolute;left:0;top:1081px;width:1200px;height:547px;background:linear-gradient(180deg,#f3f8fc 0%,var(--pale) 100%);border-top:1px solid #e3ebf3}
.card{position:absolute;top:154px;width:312px}
.card .pic{width:312px;height:178px;border:4px solid var(--white);box-shadow:0 0 0 1px #d5dde6}
.card h3{margin-top:16px;font-family:"Roboto",Arial,sans-serif;font-weight:400;font-size:19px;color:#222}
.card p{margin-top:8px;font-size:11px;line-height:17px;color:var(--muted);width:300px}
.card .read{margin-top:14px;display:inline-block;border:1.5px solid #555;padding:5px 8px;font-size:10px;font-weight:600;color:#333}
.arrow-circ{position:absolute;top:240px;width:24px;height:24px;border:1px solid #aab4bf;border-radius:50%}

/* help */
.help{position:absolute;left:0;top:1628px;width:1200px;height:559px;background:var(--white)}
.help h2{position:absolute;left:0;top:90px;width:1200px;text-align:center;font-family:"Roboto",Arial,sans-serif;font-weight:400;font-size:32px;color:#222}
.help .lead{position:absolute;left:0;top:146px;width:1200px;text-align:center;font-size:11.5px;line-height:20px;color:#555}
.field{position:absolute;border:1.5px solid #d9dfe5;box-shadow:inset 0 1px 2px rgba(0,0,0,.06);font-size:11px;color:#666;padding:10px 14px}

/* testimonial */
.quote{position:absolute;left:0;top:2187px;width:1200px;height:408px;background:linear-gradient(135deg,#4a88cc 0%,var(--blue-band) 50%,#2f68ab 100%)}
.avatar{position:absolute;left:538px;top:66px;width:124px;height:124px;border-radius:50%;border:5px solid var(--white);background:radial-gradient(circle at 50% 40%,#d9b59c 0%,#8a6a55 55%,#4a3a33 100%)}
.quote blockquote{position:absolute;left:215px;top:214px;width:780px;text-align:center;color:var(--white);font-size:12px;line-height:22px}
.quote .mark{position:absolute;left:205px;top:204px;color:var(--white);font-size:22px;font-style:italic}
.quote cite{position:absolute;left:0;top:297px;width:1200px;text-align:center;color:var(--white);font-size:14px;font-style:italic}
.q-dots{position:absolute;left:552px;top:352px;display:flex;gap:6px}
.q-dots i{width:28px;height:3px;background:rgba(255,255,255,.45)}
.q-dots i:first-child{background:var(--white)}

/* partners */
.partners{position:absolute;left:0;top:2595px;width:1200px;height:145px;background:var(--white)}
.badge{position:absolute;top:52px;height:40px;background:#3a3a3a;border-radius:6px}

/* footer */
.footer{position:absolute;left:0;top:2740px;width:1200px;height:270px;background:linear-gradient(180deg,#1a1a1a 0%,var(--footer) 100%);color:var(--white)}
.footer h4{position:absolute;top:52px;font-family:"Roboto",Arial,sans-serif;font-weight:500;font-size:16px;letter-spacing:.3px}
.footer .txt{font-size:11.5px;line-height:19px;color:#e5e5e5}
.links{position:absolute;left:722px;top:85px;list-style:none;font-size:11.5px;line-height:22.5px;color:#e5e5e5}
.contact-row{position:absolute;left:432px;display:flex;gap:14px;font-size:12px;color:#e5e5e5;line-height:18px}
.social{position:absolute;top:157px;width:30px;height:30px;border:1.5px solid var(--white);border-radius:50%}
.bottom{position:absolute;left:0;top:3010px;width:1200px;height:62px;background:var(--footer-bar);color:#cfcfcf;font-size:11px;display:flex;align-items:center;justify-content:center}
</style>
</head>
<body>

<header class="hero">
  <div class="hero-photo" role="img" aria-label="Dark blue photo of a businessman holding open hands beneath an illustration of data sheets being sorted into neat stacks"></div>
  <div class="brand">Quorvix</div>
  <nav class="nav">
    <span style="left:0">SOLUTIONS</span>
    <span style="left:99px">PRICING</span>
    <span style="left:185px">COMPANY</span>
    <span style="left:277px">GET FREE QUOTE</span>
    <span style="left:388px;top:-2px">
      <svg width="14" height="14" viewBox="0 0 14 14"><circle cx="5.5" cy="5.5" r="4" fill="none" stroke="#fff" stroke-width="2"/><line x1="8.5" y1="8.5" x2="13" y2="13" stroke="#fff" stroke-width="2"/></svg>
    </span>
  </nav>
  <h1>Turn Websites Into Structured Data feeds</h1>
  <p>Easily get structured data feeds from any website through our cloud based data as a service platform. No programming Servers or Expensive Softwares required.</p>
  <div class="btn" style="left:98px;top:387px;width:132px;height:37px">Get free Quote</div>
  <div class="hero-dots"><i></i><i></i><i></i></div>
</header>

<section class="why">
  <div class="sec-title" style="top:50px">WHY US</div>
  <div class="sec-rule" style="top:105px"></div>
  <svg class="abs" style="left:205px;top:192px" width="790" height="4"><line x1="0" y1="2" x2="790" y2="2" stroke="#9bbbe0" stroke-width="1.5" stroke-dasharray="2 3"/></svg>

  <div class="feature" style="left:85px;top:144px">
    <div class="ring"><svg width="40" height="36" viewBox="0 0 40 36"><rect x="2" y="2" width="36" height="24" rx="2" fill="#2f6fb8"/><rect x="6" y="6" width="28" height="16" fill="#fff"/><rect x="16" y="27" width="8" height="4" fill="#2f6fb8"/><rect x="11" y="31" width="18" height="3" fill="#2f6fb8"/></svg></div>
    <h3>Solve Real Problems</h3>
    <p>Quorvix provides a fully managed Big Data As A Service .You can easily plug our data feeds into your favourite</p>
    <div class="more">CLICK HERE ➜</div>
  </div>
  <div class="feature" style="left:349px;top:144px">
    <div class="ring"><svg width="40" height="40" viewBox="0 0 40 40"><line x1="34" y1="4" x2="18" y2="22" stroke="#2f6fb8" stroke-width="3"/><path d="M8 22 L22 22 L26 36 L6 36 Z" fill="none" stroke="#2f6fb8" stroke-width="2.5"/><line x1="11" y1="28" x2="11" y2="35" stroke="#2f6fb8" stroke-width="1.5"/><line x1="16" y1="28" x2="16" y2="35" stroke="#2f6fb8" stroke-width="1.5"/><line x1="21" y1="28" x2="21" y2="35" stroke="#2f6fb8" stroke-width="1.5"/></svg></div>
    <h3>Clean Data</h3>
    <p>We follow a strict quality assurance process and a Machine learning based Q&amp;A system to ensure the data</p>
    <div class="more">CLICK HERE ➜</div>
  </div>
  <div class="feature" style="left:615px;top:144px">
    <div class="ring"><svg width="40" height="34" viewBox="0 0 40 34"><rect x="2" y="2" width="36" height="30" fill="none" stroke="#2f6fb8" stroke-width="2.5"/><polyline points="7,26 15,17 21,21 32,9" fill="none" stroke="#2f6fb8" stroke-width="3"/><polygon points="27,8 34,7 33,14" fill="#2f6fb8"/></svg></div>
    <h3>Customer Success</h3>
    <p>Ensuring Customer success is our first priority. Our customer success team consists of experienced data</p>
    <div class="more">CLICK HERE ➜</div>
  </div>
  <div class="feature" style="left:875px;top:144px">
    <div class="ring"><svg width="34" height="40" viewBox="0 0 34 40"><ellipse cx="17" cy="6" rx="15" ry="5" fill="#2f6fb8"/><path d="M2 10 Q17 17 32 10 V16 Q17 23 2 16 Z" fill="#2f6fb8"/><path d="M2 20 Q17 27 32 20 V26 Q17 33 2 26 Z" fill="#2f6fb8"/><path d="M2 30 Q17 37 32 30 V34 Q17 41 2 34 Z" fill="#2f6fb8"/></svg></div>
    <h3>Data Wrangling support</h3>
    <p>Quorvix helps those who need data wrangling support by providing profiling, filtering and enrichment support.</p>
    <div class="more">CLICK HERE ➜</div>
  </div>
</section>

<section class="offer">
  <div class="sec-title" style="top:50px">OUR OFFERINGS</div>
  <div class="sec-rule" style="top:104px"></div>
  <div class="arrow-circ" style="left:48px"></div>
  <div class="arrow-circ" style="left:1128px"></div>

  <div class="card" style="left:98px">
    <div class="pic" role="img" aria-label="Illustration of an online storefront with shopping icons" style="background:linear-gradient(135deg,#f7b733 0%,#f39c12 100%)"></div>
    <h3>ECommerce</h3>
    <p>Our Ecommerce product data feeds gives you access to structured product information like pricing,, Category, reviews etc about your competitors.</p>
    <span class="read">READ MORE ⊙</span>
  </div>
  <div class="card" style="left:444px">
    <div class="pic" role="img" aria-label="Photo of two businessmen reviewing a tablet" style="background:linear-gradient(135deg,#dfe7ef 0%,#8fa4b9 55%,#3a4e66 100%)"></div>
    <h3>Lead generation</h3>
    <p>We help find quality leads for your business by extracting public data from all kind of sources like ProNet, FundBase, SeedList etc.</p>
    <span class="read">READ MORE ⊙</span>
  </div>
  <div class="card" style="left:790px">
    <div class="pic" role="img" aria-label="Photo of a person holding a tablet in front of server racks" style="background:linear-gradient(135deg,#1b2432 0%,#2e4b6e 50%,#0f1620 100%)"></div>
    <h3>SERP Tracking</h3>
    <p>Our SERP data feeds gives companies access to Search Engine rankings of any keywords from search engines like Searchly, Findr and Lookit.</p>
    <span class="read">READ MORE ⊙</span>
  </div>
</section>

<section class="help">
  <h2>WE'RE HERE TO HELP!</h2>
  <p class="lead">We're friendly and available to help solve your data extraction problems. Fill the form below to contact us.<br>Let us do the heavy lifting for you.</p>
  <div class="field" style="left:199px;top:221px;width:393px;height:37px">Name :</div>
  <div class="field" style="left:199px;top:272px;width:393px;height:37px">Email :</div>
  <div class="field" style="left:199px;top:324px;width:393px;height:37px">Phone :</div>
  <div class="field" style="left:199px;top:375px;width:393px;height:37px">Subject :</div>
  <div class="field" style="left:608px;top:221px;width:393px;height:193px">Message :</div>
  <div class="btn" style="left:510px;top:445px;width:180px;height:37px;font-family:'Roboto',Arial,sans-serif;font-weight:500;font-size:15px">SUBMIT MESSAGE</div>
</section>

<section class="quote">
  <div class="avatar" role="img" aria-label="Portrait photo of the client reviewer"></div>
  <span class="mark">“</span>
  <blockquote>Quorvix was very responsive and quick to deliver. They were happy to do 2 iterations on the initial data scrape set up to ensure we got the info we needed moving forward. They delivered great results were others had previously failed. We're excited to have found this service and will be looking to expand our work together across more data sources soon.</blockquote>
  <cite>Mara Lindqvist - Director of Business Development @ Brightlane</cite>
  <div class="q-dots"><i></i><i></i><i></i></div>
</section>

<section class="partners">
  <div class="badge" style="left:275px;width:150px"></div>
  <div class="badge" style="left:457px;width:150px"></div>
  <div class="badge" style="left:640px;width:150px"></div>
  <div class="badge" style="left:820px;width:120px"></div>
</section>

<footer class="footer">
  <h4 style="left:98px">SIGN UP FOR NEWSLETTER</h4>
  <p class="txt abs" style="left:98px;top:87px;width:250px">Get product news and data tips delivered to your inbox every month</p>
  <div class="abs" style="left:98px;top:130px;width:245px;height:42px;background:var(--white);color:#777;font-size:11px;padding:13px 14px">Enter email</div>
  <div class="btn" style="left:98px;top:184px;width:104px;height:38px;font-size:11px;font-weight:600">SUBSCRIPTION</div>

  <h4 style="left:430px">CONTACTS US</h4>
  <div class="contact-row" style="top:95px">
    <svg width="12" height="16" viewBox="0 0 12 16"><path d="M6 0 C2.7 0 0 2.6 0 5.8 C0 10 6 16 6 16 S12 10 12 5.8 C12 2.6 9.3 0 6 0 Z" fill="#fff"/><circle cx="6" cy="6" r="2.2" fill="#141414"/></svg>
    <span>Quorvix, Harbourton, Eastvale<br>Australia</span>
  </div>
  <div class="contact-row" style="top:153px">
    <svg width="13" height="13" viewBox="0 0 13 13"><path d="M2.5 0 L5 3 L3.5 5 Q5 8 8 9.5 L10 8 L13 10.5 L11 13 Q5 12.5 0 2.5 Z" fill="#fff"/></svg>
    <span>Phone: +61455019372</span>
  </div>
  <div class="contact-row" style="top:185px">
    <svg width="13" height="10" viewBox="0 0 13 10"><rect width="13" height="10" fill="#fff"/><polyline points="0,0 6.5,5.5 13,0" fill="none" stroke="#141414" stroke-width="1.3"/></svg>
    <span>info@quorvix.co</span>
  </div>

  <h4 style="left:721px">QUICK LINKS</h4>
  <ul class="links">
    <li>Home</li><li>Solutions</li><li>Pricing</li><li>Company</li><li>Get free Quote</li><li>Contact</li>
  </ul>

  <div class="abs" style="left:928px;top:82px;font-size:34px;color:var(--white)">Quorvix</div>
  <div class="social" style="left:938px"></div>
  <div class="social" style="left:973px"></div>
  <div class="social" style="left:1008px"></div>
  <div class="social" style="left:1043px"></div>
</footer>

<div class="bottom">©2015 - 2016 Quorvix, All Rights Reserved.</div>

</body>
</html>
```